verdant terraces simple classy business card design

my name is colin barrow and I run a gardening business aimed at high class verdant terraces. the business name is verdant terraces and our logo was designed on pixel harbour .My clientel are anything from residential homes to businesses. I take pride in my work and know that I offer a service like no other in my area.
The business card will be used to represent my business and I want it to be not only rememberable, but simplistic and modern. Eye catching too. Of course I would like it relatable to gardening and appealing to the correct clientel - those being garden enthusiasts, prestigious homes and businesses that are after top of the line gardening services like no other on the market.
I am not a typical lawn mowing business so I don't want a typical card design that represents that. The gardens I work with are generally million dollar properties with owners who are very garden proud looking for upkeep and guidance from me along with sometimes whole new garden designs. I want the business cards to show to my clients that I take pride, as they do, in their garden. And I want them to know from my card that I am a professional, qualified horticulturist offering them a top of the line service for life. I want them to refer my business on. I want them to look at my business card and see class and professionalism in a modern unique bold way.
The card should be simple with the possibility of the logo on the front being embossed/debossed and my details on the back the card should have a organic garden feel it's very important to me that it is absolutely perfect
I am also very open to ideas and suggestions so look forward to seeing the designs. the business logo has been supplied with this project and I want the card to be double sided

Contact info is
Colin Barrow - Managing Director / Horticulturist
Phone : 0481 526 704
Email: colinbarrow@verdantterraces.example.au

Target Market(s)

high class gardens residential and commercial

Industry/Entity Type

Gardener

Contact Information for Business Card

Contact info is
Phone : 0481 526 704

PLEASE MAKE CARD DOUBLE SIDED

Requirements
Must have
• organic simple classy modern feel
• must flow with the current logo that has been supplied with this project
• Double sided
• Must explain in a simple way that I deal with high end gardens and I'm a qualified horticulturist
Nice to have
• embossed debossed logo
Should not have
• shouldn't be to busy or cheap looking

```html
<!DOCTYPE html>
<html lang="en">
<head>
<meta charset="UTF-8">
<title>Verdant Terraces – Business Card</title>
<link rel="stylesheet" href="https://fonts.googleapis.com/css2?family=Arimo:wght@400;500&display=swap">
<style>
  :root {
    --backdrop: #e6e7e6;
    --card-white: #f2f2f3;
    --brand-green: #52894a;
    --name-green: #4d8a3f;
    --ink: #2b2b2b;
    --muted: #4a4a4a;
    --rule: #5d9450;
    --on-green: #f1f4ef;
  }
  * { box-sizing: border-box; margin: 0; padding: 0; }
  html, body {
    width: 1105px; height: 1200px; overflow: hidden;
    background: var(--backdrop);
    font-family: "Arimo", Arial, sans-serif;
  }
  .canvas { position: relative; width: 1105px; height: 1200px; }

  .card {
    position: absolute; left: 182px; width: 747px; height: 426px;
  }
  .card--front { top: 119px; background: var(--card-white); }
  .card--back  { top: 637px; background: var(--brand-green); }

  /* wordmark */
  .wordmark { position: absolute; text-align: center; font-weight: 500; text-transform: uppercase; }
  .wordmark__mark { display: block; margin: 0 auto; border-radius: 50%; }
  .wordmark__line1 { display: block; letter-spacing: 2px; line-height: 1; }
  .wordmark__line2 { display: block; letter-spacing: 19px; line-height: 1; margin-right: -19px; }

  .card--front .wordmark { right: 38px; top: 26px; width: 320px; color: var(--brand-green); }
  .card--front .wordmark__mark { width: 92px; height: 92px; background: var(--brand-green); margin-bottom: 16px; }
  .card--front .wordmark__line1 { font-size: 38px; }
  .card--front .wordmark__line2 { font-size: 21px; margin-top: 8px; }

  .card--back .wordmark { left: 0; right: 0; top: 116px; color: var(--on-green); }
  .card--back .wordmark__mark { width: 104px; height: 104px; background: var(--on-green); margin-bottom: 20px; }
  .card--back .wordmark__line1 { font-size: 44px; }
  .card--back .wordmark__line2 { font-size: 24px; margin-top: 10px; letter-spacing: 24px; margin-right: -24px; }

  /* holder details */
  .holder { position: absolute; left: 39px; top: 222px; }
  .holder__name { font-size: 25px; font-weight: 500; color: var(--name-green); }
  .holder__role { font-size: 19px; color: var(--ink); margin-top: 8px; }
  .holder__rule { position: absolute; left: 39px; right: 49px; top: 295px; height: 2px; background: var(--rule); }

  .contacts { position: absolute; left: 39px; top: 307px; list-style: none; }
  .contacts li { display: flex; align-items: center; height: 29px; font-size: 17px; color: var(--muted); }
  .contacts svg { width: 17px; height: 17px; margin-right: 10px; fill: var(--brand-green); flex: none; }

  .card__url {
    position: absolute; left: 0; right: 0; top: 364px; text-align: center;
    font-size: 18px; letter-spacing: 3.2px; color: var(--on-green);
  }
</style>
</head>
<body>
<main class="canvas">

  <section class="card card--front" aria-label="Card front">
    <div class="wordmark">
      <span class="wordmark__mark"></span>
      <span class="wordmark__line1">Verdant</span>
      <span class="wordmark__line2">Terraces</span>
    </div>

    <div class="holder">
      <p class="holder__name">Colin Barrow</p>
      <p class="holder__role">Managing Director / Horticulturist</p>
    </div>
    <div class="holder__rule"></div>

    <ul class="contacts">
      <li>
        <svg viewBox="0 0 20 20" aria-hidden="true"><path d="M2 7c0-3 4-4 8-4s8 1 8 4v1h-4V6.5c-1-.6-2.5-.8-4-.8s-3 .2-4 .8V8H2z"/><path d="M5 9h10l2 8H3z"/><circle cx="10" cy="13" r="2" fill="#f2f2f3"/></svg>
        0481 526 704
      </li>
      <li>
        <svg viewBox="0 0 20 20" aria-hidden="true"><path d="M1 4h18v12H1z"/><path d="M1 4l9 7 9-7" fill="none" stroke="#f2f2f3" stroke-width="1.6"/></svg>
        colinbarrow@verdantterraces.example.au
      </li>
      <li>
        <svg viewBox="0 0 20 20" aria-hidden="true"><circle cx="10" cy="10" r="9"/><path d="M6 5c2 0 3 1 2 3s-3 1-3 3 2 2 2 4M13 4c-1 2 1 3 2 4s0 3-2 3-1 3 0 5" fill="none" stroke="#f2f2f3" stroke-width="1.4"/></svg>
        verdantterraces.example.au
      </li>
    </ul>
  </section>

  <section class="card card--back" aria-label="Card back">
    <div class="wordmark">
      <span class="wordmark__mark"></span>
      <span class="wordmark__line1">Verdant</span>
      <span class="wordmark__line2">Terraces</span>
    </div>
    <p class="card__url">www.verdantterraces.example.au</p>
  </section>

</main>
</body>
</html>
```